Update our OBGYN business card look and info

We are an OBGYN office. Our logo is nice but would like to "woman" part of the logo to be a darker color, to contrast with the flower that surrounds it. Maybe make our practice name Bloom Harbor Health more feminine. Our practice caters to women only. All providers and staff are female.

Target Market(s)

Females 16-65.

Industry/Entity Type

Business

Contact Information for Business Card

See attached upload. The ONLY CHANGE to the information is DELETE the name Paula Renwick, Midwife and REPLACE with Dora Fintelli, Midwife

Logo Text

Bloom Harbor Health Obstetrics & Gynecology

Font styles to use
Serif
Script

Colors
85cae6
0692cd
33a6d7
85abd2
f59195
eea4c8
cadf82
fac994
d3a5cc

```html
<!DOCTYPE html>
<html lang="en">
<head>
<meta charset="utf-8">
<title>Bloom Harbor Health – Business Card</title>
<link rel="stylesheet" href="https://fonts.googleapis.com/css2?family=Cinzel:wght@500&family=Open+Sans:wght@400;600&display=swap">
<style>
  :root {
    --bg: #4a403b;
    --card: #0b0b0c;
    --card-edge: #1a1a1c;
    --blue: #33a6d7;
    --blue-deep: #0692cd;
    --green: #a9cc3c;
    --white: #f2f2f2;
    --silver: #b9b9bb;
  }
  * { margin: 0; padding: 0; box-sizing: border-box; }
  html, body { width: 1200px; height: 900px; overflow: hidden; }
  body {
    background: var(--bg);
    font-family: "Open Sans", Arial, sans-serif;
    position: relative;
  }
  .card {
    position: absolute;
    width: 540px;
    height: 309px;
    background: var(--card);
    border: 1px solid var(--card-edge);
    box-shadow: 0 10px 30px rgba(0,0,0,.45);
  }
  .card--front { left: 45px; top: 296px; }
  .card--back  { left: 615px; top: 296px; }

  /* front */
  .brand {
    position: absolute;
    left: 200px; top: 36px;
    display: flex; align-items: center; gap: 10px;
  }
  .brand__mark {
    width: 34px; height: 34px; border-radius: 50%;
    background: var(--blue);
    flex: none;
  }
  .brand__name {
    color: var(--blue);
    font-weight: 600;
    font-size: 12px;
    line-height: 1.35;
  }
  .providers {
    position: absolute;
    left: 30px; top: 128px;
    list-style: none;
    font-family: "Cinzel", "Times New Roman", serif;
    font-weight: 500;
    font-size: 17px;
    line-height: 22px;
  }
  .providers .md { color: var(--blue); }
  .providers .midwife { color: var(--green); }
  .address {
    position: absolute;
    left: 30px; top: 248px;
    color: var(--white);
    font-size: 13px;
    line-height: 18px;
    font-style: normal;
  }
  .contact {
    position: absolute;
    right: 26px; top: 152px;
    list-style: none;
    color: var(--white);
    font-size: 12.5px;
    line-height: 19px;
    text-align: right;
  }
  .contact li { display: flex; justify-content: flex-end; align-items: center; gap: 6px; }
  .contact svg { width: 11px; height: 11px; flex: none; }

  /* back */
  .brand--back {
    left: 0; right: 0; top: 0; bottom: 0;
    justify-content: center;
    gap: 14px;
  }
  .brand--back .brand__mark {
    width: 58px; height: 58px;
    background: var(--silver);
  }
  .brand--back .brand__name {
    color: var(--silver);
    font-size: 15px;
    letter-spacing: .3px;
  }
</style>
</head>
<body>

<section class="card card--front" aria-label="Business card front">
  <div class="brand">
    <span class="brand__mark"></span>
    <p class="brand__name">BLOOM HARBOR HEALTH<br>Obstetrics &amp; Gynecology</p>
  </div>

  <ul class="providers">
    <li class="md">Helena Marsh, MD</li>
    <li class="md">Karen Whitfield, MD</li>
    <li class="md">Karen Whitfield, MD</li>
    <li class="midwife">Dora Fintelli, Midwife</li>
    <li class="midwife">Jenna Calloway, Midwife</li>
  </ul>

  <address class="address">418 Linden Ave. Ste 2A<br>Harborview, GA 30012-4417</address>

  <ul class="contact">
    <li>555-014-2738
      <svg viewBox="0 0 24 24" aria-hidden="true"><path fill="#33a6d7" d="M6.6 10.8a15.1 15.1 0 0 0 6.6 6.6l2.2-2.2c.3-.3.7-.4 1-.2 1.1.4 2.3.6 3.6.6.6 0 1 .4 1 1V20c0 .6-.4 1-1 1A17 17 0 0 1 3 4c0-.6.4-1 1-1h3.5c.6 0 1 .4 1 1 0 1.3.2 2.5.6 3.6.1.3 0 .7-.2 1z"/></svg>
    </li>
    <li>555-014-2153
      <svg viewBox="0 0 24 24" aria-hidden="true"><rect x="4" y="3" width="16" height="18" rx="2" fill="#33a6d7"/><rect x="7" y="6" width="10" height="4" fill="#0b0b0c"/><rect x="7" y="13" width="2" height="2" fill="#0b0b0c"/><rect x="11" y="13" width="2" height="2" fill="#0b0b0c"/><rect x="15" y="13" width="2" height="2" fill="#0b0b0c"/></svg>
    </li>
    <li>www.bloomharborhealth.com
      <svg viewBox="0 0 24 24" aria-hidden="true"><circle cx="12" cy="12" r="10" fill="#33a6d7"/><path d="M2 12h20M12 2c3 3 3 17 0 20M12 2c-3 3-3 17 0 20" stroke="#0b0b0c" stroke-width="1.6" fill="none"/></svg>
    </li>
  </ul>
</section>

<section class="card card--back" aria-label="Business card back">
  <div class="brand brand--back">
    <span class="brand__mark"></span>
    <p class="brand__name">BLOOM HARBOR HEALTH<br>Obstetrics &amp; Gynecology</p>
  </div>
</section>

</body>
</html>
```